Real Estate agent needs flyer/folder to contain bio and overview of services

I'm including files of the layout of the small folder. The folder is 6 1/2 across and 9 1/2 inches long. It will have a front & back cover and then writing on the 2 inside pages.

I am sending a few files to incorporate into the flyer, 1 new logo to use and 2 files which are coloring ideas.

Colors

Designer to choose colors to be used in the design.

```html
<!DOCTYPE html>
<html lang="en">
<head>
<meta charset="utf-8">
<title>Folder Back Cover</title>
<link rel="stylesheet" href="https://fonts.googleapis.com/css2?family=Arimo:ital,wght@0,400;0,700;1,400;1,700&family=Open+Sans&display=swap">
<style>
  :root {
    --backdrop: #f3e3b3;
    --paper: #ffffff;
    --ink: #111111;
    --royal: #0b4793;
    --navy: #101a72;
    --hair: #dcc08a;
    --skin: #e9c9ad;
    --blazer: #262626;
    --blouse: #f4f2ee;
  }
  html, body {
    margin: 0;
    padding: 0;
    width: 1200px;
    height: 1200px;
    overflow: hidden;
    background: var(--backdrop);
  }
  .canvas {
    position: relative;
    width: 1200px;
    height: 1200px;
    background: var(--backdrop);
  }
  .side-label {
    position: absolute;
    left: 1085px;
    top: 34px;
    font-family: "Open Sans", sans-serif;
    font-size: 18px;
    color: var(--ink);
  }
  .cover {
    position: absolute;
    left: 218px;
    top: 26px;
    width: 781px;
    height: 1140px;
    background: var(--paper);
    border: 1.5px solid var(--ink);
    box-sizing: border-box;
    overflow: hidden;
  }
  .agent-photo {
    position: absolute;
    left: 30px;
    top: 700px;
    width: 250px;
    height: 350px;
    background:
      radial-gradient(ellipse 30% 26% at 62% 34%, var(--skin) 0%, rgba(233,201,173,0.85) 55%, rgba(233,201,173,0) 100%),
      radial-gradient(ellipse 48% 44% at 52% 32%, var(--hair) 0%, rgba(220,192,138,0.9) 55%, rgba(220,192,138,0) 100%),
      radial-gradient(ellipse 14% 30% at 70% 88%, var(--blouse) 0%, rgba(244,242,238,0) 100%),
      radial-gradient(ellipse 58% 34% at 55% 92%, var(--blazer) 0%, rgba(38,38,38,0.9) 55%, rgba(38,38,38,0) 100%);
  }
  .corner-bands {
    position: absolute;
    left: 0;
    top: 0;
    width: 781px;
    height: 1140px;
  }
  .referral-note {
    position: absolute;
    left: 274px;
    top: 782px;
    margin: 0;
    font-family: "Arimo", sans-serif;
    font-style: italic;
    font-size: 14.6px;
    line-height: 18.4px;
    color: var(--ink);
    white-space: nowrap;
  }
  .contact {
    position: absolute;
    left: 274px;
    top: 869px;
    margin: 0;
    font-family: "Arimo", sans-serif;
    font-style: italic;
    font-weight: 700;
    font-size: 17.6px;
    line-height: 21.6px;
    color: var(--ink);
    white-space: nowrap;
  }
  .brokerage {
    position: absolute;
    left: 520px;
    top: 937px;
    width: 176px;
    display: flex;
    align-items: center;
    justify-content: center;
    gap: 8px;
    font-family: "Arimo", sans-serif;
    font-weight: 700;
    font-size: 19px;
    color: var(--navy);
    text-transform: uppercase;
    white-space: nowrap;
  }
  .brokerage-dot {
    width: 14px;
    height: 14px;
    border-radius: 50%;
    background: var(--navy);
    flex: none;
  }
</style>
</head>
<body>
<div class="canvas">
  <div class="side-label">BACK</div>
  <section class="cover">
    <div class="agent-photo" role="img" aria-label="Portrait photo of the agent with long blonde hair, dark blazer and white blouse"></div>
    <svg class="corner-bands" viewBox="0 0 781 1140" aria-hidden="true">
      <polygon fill="var(--navy)" points="485,1102 783,1016 783,1142 585,1142"/>
      <polygon fill="var(--royal)" points="-2,920 585,1142 -2,1142"/>
    </svg>
    <p class="referral-note">Along with being your Realtor, I’m a lifelong resource for all things<br>home-related &amp; beyond…if you need a great referral for anything<br>at all, call me!&nbsp; I can’t wait to work with you!</p>
    <p class="contact">
      Carla Moretti<br>
      949 555 0142<br>
      Carla@morettihomes.com<br>
      www.morettihomes.com
    </p>
    <div class="brokerage"><span class="brokerage-dot"></span>Skyline Realty</div>
  </section>
</div>
</body>
</html>
```